International Clinical Software Company needs a new business card design

We are looking for a new business card design for our company that has recently expanded into the UK market, making us a multinational company.
After having rebranded our website and produced a new style guide, we are looking for a business card that is creative and attention grabbing, while being consistent with the style and colour scheme used on the new website, www.plumvora.example
We produce care management technology for the aged care market, but the main aspect we aim to communicate is the human element of our software, and the way it assists in providing better care for aged people, and stronger relationships between aged people and the staff that care for them.
Our current business card is a dark green with gold text, which makes the text quite difficult to read, not very aesthetically appealing and the colour scheme looks quite dated.
We would like something fresh and modern, that can still be colourful but doesn't use large blocks of dark colour, and uses the colours within our logo.
Something tying in with the leaves that are used in our logo could work quite nicely, along with the Autumn/Fall colours of soft greens, yellows and reds (also in our existing logo). However also happy to look at fresh, completely out of the box ideas we may not have yet considered.
Target Market(s)
The people that receive this business card work in the aged card or health industry and are either corporate/management level staff or clinical (Registered Nurses, care workers etc.)
Industry/Entity Type
Health Product
Contact Information for Business Card
Company Name - BrindlewayCare
Company locations: United Kingdom, Australia, New Zealand
Staff Details:
Staff name: Derek Mallow
Staff job title: Executive Chairman
Staff email: d.mallow@plumvora.example
Office phone number: 01742 918576
Font styles to use
Other font styles liked:
- Calibri
Requirements
Must have
- Must include the BrindlewayCare brand name in it's current font
- Must include logo (3 leaves in gold circle)
- Must include Business Card Details
Nice to have
- Elements of gold
- White space
- Something autumn themed but not too cliched
Should not have
- No blue - used by a major competitor and we would like to differentiate from them
- Large blocks of dark green colour (the green that appears in our leaves on the logo on our current business card is the background colour and it is far too dark)

```html
<!DOCTYPE html>
<html lang="en">
<head>
<meta charset="utf-8">
<title>BrindlewayCare – Business Card</title>
<link rel="stylesheet" href="https://fonts.googleapis.com/css2?family=Carlito:wght@400;700&display=swap">
<style>
  :root {
    --canvas-bg: #ecebe7;
    --card-white: #ffffff;
    --gold: #b9a97e;
    --gold-deep: #a8976a;
    --crimson: #b5173f;
    --text-grey: #5b5b5b;
    --text-white: #ffffff;
  }
  * { margin: 0; padding: 0; box-sizing: border-box; }
  html, body {
    width: 1200px;
    height: 950px;
    overflow: hidden;
    background: var(--canvas-bg);
    font-family: "Carlito", "Calibri", Arial, sans-serif;
  }
  .canvas {
    position: relative;
    width: 1200px;
    height: 950px;
  }
  .business-card {
    position: absolute;
    left: 75px;
    top: 175px;
    width: 1050px;
    height: 600px;
    background: var(--card-white);
    box-shadow: 0 10px 30px rgba(0,0,0,0.18);
    overflow: hidden;
  }
  .card-bands {
    position: absolute;
    inset: 0;
  }
  .band-gold { fill: var(--gold); }
  .band-crimson { fill: var(--crimson); }

  .staff {
    position: absolute;
    right: 48px;
    top: 34px;
    text-align: right;
    color: var(--text-white);
  }
  .staff-name {
    font-size: 38px;
    font-weight: 700;
    line-height: 1.1;
  }
  .staff-title {
    font-size: 25px;
    font-weight: 400;
    margin-top: 4px;
  }

  .reach {
    position: absolute;
    right: 48px;
    top: 292px;
    text-align: right;
    color: var(--text-grey);
  }
  .social-dots {
    display: flex;
    justify-content: flex-end;
    gap: 6px;
    margin-bottom: 10px;
  }
  .social-dot {
    width: 20px;
    height: 20px;
    border-radius: 50%;
    background: var(--gold);
  }
  .locations {
    font-size: 25px;
    line-height: 1.3;
  }

  .brand {
    position: absolute;
    left: 62px;
    top: 332px;
    display: flex;
    align-items: center;
    gap: 18px;
  }
  .brand-circle {
    width: 116px;
    height: 116px;
    border-radius: 50%;
    border: 4px solid var(--gold);
  }
  .brand-name {
    font-size: 46px;
    font-weight: 400;
    color: var(--gold-deep);
    margin-top: -44px;
  }

  .contacts {
    position: absolute;
    left: 66px;
    top: 470px;
    list-style: none;
    color: var(--text-grey);
    font-size: 25px;
  }
  .contact-item {
    display: flex;
    align-items: center;
    gap: 12px;
    line-height: 36px;
  }
  .contact-icon {
    width: 22px;
    height: 22px;
    flex: none;
  }
  .contact-icon * { fill: var(--gold); }
</style>
</head>
<body>
<main class="canvas">
  <article class="business-card">
    <svg class="card-bands" viewBox="0 0 1050 600" width="1050" height="600" aria-hidden="true">
      <path class="band-gold" d="M0,0 H1050 V196 C700,150 300,150 0,250 Z"/>
      <path class="band-crimson" d="M0,290 C300,182 700,180 1050,218 V256 C700,220 300,218 0,290 Z"/>
    </svg>

    <header class="staff">
      <h1 class="staff-name">Derek Mallow</h1>
      <p class="staff-title">Executive Chairman</p>
    </header>

    <section class="reach">
      <div class="social-dots">
        <span class="social-dot"></span>
        <span class="social-dot"></span>
        <span class="social-dot"></span>
      </div>
      <p class="locations">United Kingdom<br>Australia, New Zealand</p>
    </section>

    <div class="brand">
      <span class="brand-circle"></span>
      <span class="brand-name">BrindlewayCare</span>
    </div>

    <ul class="contacts">
      <li class="contact-item">
        <svg class="contact-icon" viewBox="0 0 22 22" aria-hidden="true">
          <circle cx="11" cy="11" r="11"/>
          <path d="M7 6 h3 l1 3 -1.5 1 a7 7 0 0 0 3.5 3.5 l1 -1.5 3 1 v3 a1 1 0 0 1 -1 1 A11 11 0 0 1 6 7 a1 1 0 0 1 1 -1z" style="fill:#fff"/>
        </svg>
        <span>01742 918576</span>
      </li>
      <li class="contact-item">
        <svg class="contact-icon" viewBox="0 0 22 22" aria-hidden="true">
          <rect x="1" y="4" width="20" height="14" rx="2"/>
          <path d="M2 5 L11 12 L20 5" style="fill:none;stroke:#fff;stroke-width:1.6"/>
        </svg>
        <span>d.mallow@plumvora.example</span>
      </li>
      <li class="contact-item">
        <svg class="contact-icon" viewBox="0 0 22 22" aria-hidden="true">
          <circle cx="11" cy="11" r="11"/>
          <g style="fill:none;stroke:#fff;stroke-width:1.4">
            <circle cx="11" cy="11" r="6"/>
            <ellipse cx="11" cy="11" rx="2.6" ry="6"/>
            <line x1="5" y1="11" x2="17" y2="11"/>
          </g>
        </svg>
        <span>www.plumvora.example</span>
      </li>
    </ul>
  </article>
</main>
</body>
</html>
```